MRT Property - Business Cards

Looking for a business card & general letterhead, signage etc design for our new logo.

Colours:
000a20
0056a2
00b5ef
0088ce
68cef2

Fonts:
Poppins
Karla

Please keep look and feel of new brand - example in the zip package I sent.

```html
<!DOCTYPE html>
<html lang="en">
<head>
<meta charset="utf-8">
<title>MRT Property – Stationery</title>
<link href="https://fonts.googleapis.com/css2?family=Poppins:wght@400;500;600;700&display=swap" rel="stylesheet">
<style>
  :root {
    --ink: #000a20;
    --navy: #0056a2;
    --cyan: #00b5ef;
    --mid: #0088ce;
    --sky: #68cef2;
    --paper: #ffffff;
    --backdrop-top: #dcdcdc;
    --backdrop-bottom: #c4c4c4;
    --faint: #eef3fa;
  }
  * { box-sizing: border-box; margin: 0; padding: 0; }
  html, body { width: 1200px; height: 686px; overflow: hidden; }
  body {
    background: linear-gradient(180deg, var(--backdrop-top), #ececec 50%, var(--backdrop-bottom));
    font-family: "Poppins", sans-serif;
    color: var(--ink);
    position: relative;
  }
  .sheet {
    position: absolute;
    background: var(--paper);
    box-shadow: 0 6px 18px rgba(0,0,0,0.18);
  }
  .wordmark {
    display: flex; align-items: center; gap: 8px;
    font-family: "Poppins", sans-serif;
    font-weight: 700;
    color: var(--navy);
    white-space: nowrap;
  }
  .wordmark .dot { border-radius: 50%; background: var(--mid); flex: none; }

  /* Letterhead */
  .letterhead { left: 80px; top: 40px; width: 430px; height: 606px; }
  .letterhead .wordmark { position: absolute; top: 48px; right: 40px; font-size: 20px; }
  .letterhead .wordmark .dot { width: 12px; height: 12px; }
  .letterhead .backdrop-name {
    position: absolute; left: 0; right: 0; top: 250px;
    text-align: center; font-weight: 700; font-size: 54px;
    color: var(--faint);
  }
  .letterhead .footer {
    position: absolute; left: 40px; right: 40px; bottom: 36px;
    border-top: 1.5px solid var(--mid);
    padding-top: 12px;
    display: grid; grid-template-columns: auto auto; gap: 8px 18px;
    font-size: 8.5px;
  }
  .contact { display: flex; align-items: center; gap: 5px; white-space: nowrap; }
  .contact svg { width: 9px; height: 9px; flex: none; fill: var(--mid); }

  /* Cards */
  .card { width: 500px; height: 286px; left: 620px; }
  .card-front { top: 40px; }
  .card-back { top: 360px; display: flex; align-items: center; justify-content: center; }
  .card-back .wordmark { font-size: 38px; gap: 14px; }
  .card-back .wordmark .dot { width: 22px; height: 22px; }

  .card-front .wordmark { position: absolute; left: 44px; top: 70px; font-size: 24px; }
  .card-front .wordmark .dot { width: 14px; height: 14px; }
  .card-front .divider {
    position: absolute; left: 260px; top: 48px; width: 1px; height: 150px;
    background: var(--mid);
  }
  .card-front .person { position: absolute; left: 284px; top: 56px; }
  .person .name { font-size: 20px; font-weight: 700; color: var(--navy); line-height: 1.1; }
  .person .name .surname { font-weight: 400; color: var(--sky); }
  .person .role { font-size: 10px; font-weight: 500; margin-bottom: 14px; }
  .person .contact { font-size: 9.5px; margin-bottom: 6px; }
  .card-front .address {
    position: absolute; left: 44px; bottom: 30px; font-size: 9.5px;
  }
</style>
</head>
<body>

<svg width="0" height="0" style="position:absolute">
  <defs>
    <symbol id="icon-phone" viewBox="0 0 24 24"><path d="M6.6 10.8a15 15 0 0 0 6.6 6.6l2.2-2.2a1 1 0 0 1 1-.25 11.4 11.4 0 0 0 3.6.57 1 1 0 0 1 1 1V20a1 1 0 0 1-1 1A17 17 0 0 1 3 4a1 1 0 0 1 1-1h3.5a1 1 0 0 1 1 1c0 1.25.2 2.45.57 3.57a1 1 0 0 1-.25 1z"/></symbol>
    <symbol id="icon-pin" viewBox="0 0 24 24"><path d="M12 2a7 7 0 0 0-7 7c0 5.2 7 13 7 13s7-7.8 7-13a7 7 0 0 0-7-7zm0 9.5A2.5 2.5 0 1 1 12 6.5a2.5 2.5 0 0 1 0 5z"/></symbol>
    <symbol id="icon-mail" viewBox="0 0 24 24"><path d="M3 5h18a1 1 0 0 1 1 1v12a1 1 0 0 1-1 1H3a1 1 0 0 1-1-1V6a1 1 0 0 1 1-1zm9 7.5L4 7.5V9l8 5 8-5V7.5z"/></symbol>
    <symbol id="icon-web" viewBox="0 0 24 24"><path d="M12 2a10 10 0 1 0 0 20 10 10 0 0 0 0-20zm6.9 6h-3a15 15 0 0 0-1.3-3.9A8 8 0 0 1 18.9 8zM12 4a13 13 0 0 1 1.9 4h-3.8A13 13 0 0 1 12 4zM4.3 14a8 8 0 0 1 0-4h3.4a16 16 0 0 0 0 4zm.8 2h3a15 15 0 0 0 1.3 3.9A8 8 0 0 1 5.1 16zm3-8h-3a8 8 0 0 1 4.3-3.9A15 15 0 0 0 8.1 8zM12 20a13 13 0 0 1-1.9-4h3.8A13 13 0 0 1 12 20zm2.3-6H9.7a14 14 0 0 1 0-4h4.6a14 14 0 0 1 0 4zm.3 5.9a15 15 0 0 0 1.3-3.9h3a8 8 0 0 1-4.3 3.9zM16.3 14a16 16 0 0 0 0-4h3.4a8 8 0 0 1 0 4z"/></symbol>
  </defs>
</svg>

<section class="sheet letterhead">
  <div class="wordmark"><span class="dot"></span>MRT Property</div>
  <div class="backdrop-name" aria-hidden="true">MRT Property</div>
  <footer class="footer">
    <span class="contact"><svg><use href="#icon-phone"/></svg>+61 2 9000 1234</span>
    <span class="contact"><svg><use href="#icon-mail"/></svg>info@mrtproperty.com.au</span>
    <span class="contact"><svg><use href="#icon-pin"/></svg>Suite 4.12, Level 4, 18 Harbour Lane, Rhodes NSW 2138</span>
    <span class="contact"><svg><use href="#icon-web"/></svg>www.mrtproperty.com.au</span>
  </footer>
</section>

<section class="sheet card card-front">
  <div class="wordmark"><span class="dot"></span>MRT Property</div>
  <div class="divider"></div>
  <div class="person">
    <div class="name">Liam <span class="surname">Porter</span></div>
    <div class="role">Director</div>
    <div class="contact"><svg><use href="#icon-phone"/></svg>+61 2 9000 1234</div>
    <div class="contact"><svg><use href="#icon-web"/></svg>www.mrtproperty.com.au</div>
    <div class="contact"><svg><use href="#icon-mail"/></svg>info@mrtproperty.com.au</div>
  </div>
  <div class="address">Suite 4.12, Level 4, 18 Harbour Lane, Rhodes NSW 2138</div>
</section>

<section class="sheet card card-back">
  <div class="wordmark"><span class="dot"></span>MRT Property</div>
</section>

</body>
</html>
```